Mosquito and outdoor pest management

The uploaded logo must be integrated as the main theme of the card. I would like it to be modern and eye catching. Maybe some backround images or light silver metallic background.
Space enough at the base for contact info to be put in- phone numbers,emails,names,website.
Space on the back for short blog and lines for hand writing..calling card.
Commercial- golf courses, schools, outdoor function properties, pre event treatments.
Residential- retirement villages, townhome complexes and general houses
Management

```html
<!DOCTYPE html>
<html lang="en">
<head>
<meta charset="UTF-8">
<title>Bayline Pest Care – Business Card</title>
<link rel="stylesheet" href="https://fonts.googleapis.com/css2?family=Noto+Serif:wght@700&family=Arimo:wght@400&display=swap">
<style>
  :root{
    --red:#e8273a;
    --ink:#1f1f1f;
    --paper:#ffffff;
    --backdrop:#e9e7e4;
    --rule:#2b2b2b;
    --band-edge:#e6e6e6;
  }
  *{margin:0;padding:0;box-sizing:border-box}
  html,body{width:1200px;height:892px;overflow:hidden;background:var(--backdrop)}
  .canvas{position:relative;width:1200px;height:892px}
  .card{position:absolute;left:250px;width:700px;height:400px;background:var(--paper);
        box-shadow:0 4px 18px rgba(0,0,0,.18);overflow:hidden}
  .card--front{top:30px}
  .card--back{top:462px}
  .card__bands{position:absolute;inset:0}
  .brand{position:absolute;display:flex;align-items:center;gap:14px;
         font-family:"Arimo",sans-serif;font-weight:400;color:var(--ink);white-space:nowrap}
  .brand__dot{width:16px;height:16px;border-radius:50%;background:var(--red);flex:none}
  .card--front .brand{left:70px;top:112px;font-size:40px}
  .front__rule{position:absolute;left:70px;right:70px;top:180px;height:1.5px;background:var(--rule)}
  .contact{position:absolute;left:160px;top:194px;font-family:"Arimo",sans-serif;color:var(--ink)}
  .contact__name{font-family:"Noto Serif",serif;font-weight:700;color:var(--red);font-size:27px;margin-bottom:6px}
  .contact__line{font-size:16px;line-height:22px}
  .card--back .brand{right:46px;top:40px;font-size:38px}
  .back__rule{position:absolute;left:40px;right:40px;top:112px;height:1.5px;background:var(--rule)}
  .services{position:absolute;top:138px;left:60px;right:40px;display:flex;gap:50px}
  .services__col{flex:1}
  .services__title{font-family:"Noto Serif",serif;font-weight:700;color:var(--red);font-size:30px;margin-bottom:12px}
  .services__list{list-style:none;font-family:"Arimo",sans-serif;font-size:18px;color:var(--ink);line-height:28px}
  .services__list li::before{content:"*";color:var(--red);font-size:26px;margin-right:10px;vertical-align:-6px}
</style>
</head>
<body>
<main class="canvas">

  <section class="card card--front" aria-label="Business card front">
    <svg class="card__bands" width="700" height="400" viewBox="0 0 700 400" aria-hidden="true">
      <path d="M0 0 H700 V70 Q350 -10 0 70 Z" fill="var(--red)"/>
      <path d="M0 84 Q350 4 700 84" fill="none" stroke="var(--band-edge)" stroke-width="10"/>
      <path d="M0 92 Q350 12 700 92" fill="none" stroke="var(--rule)" stroke-width="4"/>
      <path d="M0 400 H700 V335 Q350 410 0 335 Z" fill="var(--red)"/>
      <path d="M0 320 Q350 396 700 320" fill="none" stroke="var(--band-edge)" stroke-width="10"/>
      <path d="M0 312 Q350 388 700 312" fill="none" stroke="var(--rule)" stroke-width="4"/>
    </svg>
    <div class="brand"><span class="brand__dot"></span>Bayline Pest Care</div>
    <div class="front__rule"></div>
    <div class="contact">
      <p class="contact__name">Owen Hartley</p>
      <p class="contact__line">+1 555 010 2040</p>
      <p class="contact__line">hello@baylinepest.com</p>
      <p class="contact__line">www.baylinepest.com</p>
    </div>
  </section>

  <section class="card card--back" aria-label="Business card back">
    <div class="brand"><span class="brand__dot"></span>Bayline Pest Care</div>
    <div class="back__rule"></div>
    <div class="services">
      <div class="services__col">
        <h2 class="services__title">Commercial</h2>
        <ul class="services__list">
          <li>golf courses</li>
          <li>outdoor function properties</li>
          <li>pre event treatments</li>
        </ul>
      </div>
      <div class="services__col">
        <h2 class="services__title">Residential</h2>
        <ul class="services__list">
          <li>retirement villages</li>
          <li>townhome complexes</li>
          <li>general houses</li>
        </ul>
      </div>
    </div>
  </section>

</main>
</body>
</html>
```